New Bicycle shop business card

Hi!
I'm looking for a business card for my new proffesional bike mechanics shop. This shop is only for fixing broken bikes and not selling bikes.
Peferbly a modern and sleek and modern design.
Colors: black, grey, red, white
Information:
Name: Rijwielwerkplaats Vanhoutte
Shop owner: Bart Vanhoutte & Marieke Segers
Website: www.rijwielwerkplaats-vanhoutte.be
Email: info@rijwielwerkplaats-vanhoutte.be
Phone number: +32471902368
Street adres: Kerkweg 46
9940 Bellebeke
Slogan/shop information: Herstellingen van alle merken.
Logo: see files.
Target Market(s)
People who seek a mechanic to fix or upgrade their bikes.
Contact Information for Business Card
Information:
Website: info@rijwielwerkplaats-vanhoutte.be
9940 Bellebeke
Logo: see files.

```html
<!DOCTYPE html>
<html lang="nl">
<head>
<meta charset="utf-8">
<title>Rijwielwerkplaats Vanhoutte – Business Card</title>
<link rel="stylesheet" href="https://fonts.googleapis.com/css2?family=Open+Sans:wght@400;600;700;800&display=swap">
<style>
  :root {
    --page-bg: #3a3a3d;
    --card-bg: #060607;
    --brand-red: #e8274b;
    --ink-white: #ffffff;
    --ink-grey: #b8b8bb;
    --divider: #1f1f22;
  }
  * { box-sizing: border-box; margin: 0; padding: 0; }
  html, body {
    width: 1200px; height: 1000px; overflow: hidden;
    background: var(--page-bg);
    font-family: "Open Sans", Arial, sans-serif;
    color: var(--ink-white);
  }
  .canvas {
    position: relative; width: 1200px; height: 1000px;
  }
  .card {
    position: absolute; left: 220px;
    width: 760px; height: 434px;
    background: var(--card-bg);
    border-radius: 22px;
    box-shadow: 0 18px 40px rgba(0,0,0,.45);
    overflow: hidden;
  }
  .card--brand { top: 50px; }
  .card--contact { top: 516px; }

  .wordmark {
    display: flex; flex-direction: column; align-items: center; gap: 14px;
  }
  .wordmark__dot {
    width: 64px; height: 64px; border-radius: 50%;
    background: var(--brand-red);
  }
  .wordmark__name {
    font-weight: 800; font-size: 34px; letter-spacing: 1.5px;
    text-transform: uppercase; color: var(--ink-white); text-align: center;
    line-height: 1.15;
  }

  .card--brand .wordmark { position: absolute; left: 0; right: 0; top: 104px; }
  .tagline {
    position: absolute; left: 0; right: 0; top: 320px;
    text-align: center; font-size: 17px; font-weight: 600;
    letter-spacing: .4px;
  }

  .card--contact .wordmark { position: absolute; left: 0; right: 0; top: 36px; }
  .card--contact .wordmark__dot { width: 56px; height: 56px; }
  .card--contact .wordmark__name { font-size: 30px; }

  .details {
    position: absolute; left: 40px; right: 40px; top: 200px; bottom: 40px;
    display: grid; grid-template-columns: 1fr 1px 1fr; column-gap: 30px;
  }
  .divider { background: var(--divider); }
  .owners { text-align: right; padding-top: 14px; }
  .owners__label { color: var(--brand-red); font-size: 20px; font-weight: 600; }
  .owners__names { font-size: 19px; font-weight: 800; margin-top: 2px; }
  .owners__address { font-size: 16px; margin-top: 8px; line-height: 1.4; }

  .company__name { color: var(--brand-red); font-size: 20px; font-weight: 800; }
  .company__role { font-size: 16px; font-weight: 700; margin-top: 2px; }
  .contact-list { list-style: none; margin-top: 12px; }
  .contact-list li {
    display: flex; align-items: center; gap: 10px;
    font-size: 14.5px; line-height: 1.85; white-space: nowrap;
  }
  .contact-list svg { width: 15px; height: 15px; flex: none; fill: var(--brand-red); }
</style>
</head>
<body>
<main class="canvas">

  <section class="card card--brand" aria-label="Business card front">
    <div class="wordmark">
      <span class="wordmark__dot"></span>
      <span class="wordmark__name">Rijwielwerkplaats<br>Vanhoutte</span>
    </div>
    <p class="tagline">Herstellingen van alle merken.</p>
  </section>

  <section class="card card--contact" aria-label="Business card back">
    <div class="wordmark">
      <span class="wordmark__dot"></span>
      <span class="wordmark__name">Rijwielwerkplaats Vanhoutte</span>
    </div>

    <div class="details">
      <div class="owners">
        <p class="owners__label">Shop owner:</p>
        <p class="owners__names">Bart Vanhoutte &amp; Marieke Segers</p>
        <p class="owners__address">Kerkweg 46<br>9940 Bellebeke</p>
      </div>
      <span class="divider"></span>
      <div class="company">
        <p class="company__name">Rijwielwerkplaats Vanhoutte</p>
        <p class="company__role">General Manager</p>
        <ul class="contact-list">
          <li>
            <svg viewBox="0 0 24 24" aria-hidden="true"><path d="M6.6 10.8a15.1 15.1 0 0 0 6.6 6.6l2.2-2.2a1 1 0 0 1 1-.25 11.4 11.4 0 0 0 3.6.57 1 1 0 0 1 1 1V20a1 1 0 0 1-1 1A17 17 0 0 1 3 4a1 1 0 0 1 1-1h3.5a1 1 0 0 1 1 1c0 1.25.2 2.45.57 3.6a1 1 0 0 1-.25 1z"/></svg>
            +32471902368
          </li>
          <li>
            <svg viewBox="0 0 24 24" aria-hidden="true"><path d="M3 5h18a1 1 0 0 1 1 1v12a1 1 0 0 1-1 1H3a1 1 0 0 1-1-1V6a1 1 0 0 1 1-1zm1 2.3V17h16V7.3l-8 5.4z"/></svg>
            info@rijwielwerkplaats-vanhoutte.be
          </li>
          <li>
            <svg viewBox="0 0 24 24" aria-hidden="true"><path d="M12 2a10 10 0 1 0 0 20 10 10 0 0 0 0-20zm6.9 6h-3a15.6 15.6 0 0 0-1.4-3.6A8 8 0 0 1 18.9 8zM12 4a14 14 0 0 1 1.9 4h-3.8A14 14 0 0 1 12 4zM4.3 14a8 8 0 0 1 0-4h3.4a16.5 16.5 0 0 0 0 4zm.8 2h3a15.6 15.6 0 0 0 1.4 3.6A8 8 0 0 1 5.1 16zM8.1 8h-3a8 8 0 0 1 4.4-3.6A15.6 15.6 0 0 0 8.1 8zM12 20a14 14 0 0 1-1.9-4h3.8A14 14 0 0 1 12 20zm2.3-6H9.7a14.7 14.7 0 0 1 0-4h4.6a14.7 14.7 0 0 1 0 4zm.2 5.6a15.6 15.6 0 0 0 1.4-3.6h3a8 8 0 0 1-4.4 3.6zm1.8-5.6a16.5 16.5 0 0 0 0-4h3.4a8 8 0 0 1 0 4z"/></svg>
            www.rijwielwerkplaats-vanhoutte.be
          </li>
        </ul>
      </div>
    </div>
  </section>

</main>
</body>
</html>
```